Veldmark Supplies Business Card

Professional business card that stand out to our potential customers. Front and back with clean modern design

Industry/Entity Type

Oil and gas

Contact Information for Business Card

Name, address, website , office phone and cell number

Requirements
Must have
• Editable files for each employee

```html
<!DOCTYPE html>
<html lang="en">
<head>
<meta charset="UTF-8">
<title>Veldmark Supplies Business Card</title>
<link rel="stylesheet" href="https://fonts.googleapis.com/css2?family=Roboto:wght@400;500;700&display=swap">
<style>
  :root {
    --backdrop: #3b3b3d;
    --card-white: #ffffff;
    --brand-red: #c8101a;
    --brand-red-deep: #9e0c12;
    --ink-light: #ffffff;
    --shadow: rgba(0, 0, 0, 0.45);
  }
  * { margin: 0; padding: 0; box-sizing: border-box; }
  html, body {
    width: 1200px;
    height: 694px;
    overflow: hidden;
    background: var(--backdrop);
    font-family: "Roboto", Arial, sans-serif;
  }
  .canvas {
    position: relative;
    width: 1200px;
    height: 694px;
    display: flex;
    align-items: center;
    justify-content: center;
    gap: 60px;
  }
  .card {
    position: relative;
    width: 500px;
    height: 286px;
    border-radius: 26px;
    box-shadow: 0 14px 30px var(--shadow);
    overflow: hidden;
  }
  .card-front {
    background: var(--card-white);
    display: flex;
    align-items: center;
    justify-content: center;
  }
  .brand-lockup {
    display: flex;
    align-items: center;
    gap: 14px;
  }
  .brand-square {
    width: 34px;
    height: 34px;
  }
  .card-front .brand-square { background: var(--brand-red); }
  .card-front .brand-name {
    color: var(--brand-red);
    font-weight: 700;
    font-size: 34px;
    letter-spacing: 1px;
    text-transform: uppercase;
  }
  .card-back {
    background: radial-gradient(circle at 30% 30%, var(--brand-red) 0%, var(--brand-red-deep) 100%);
    color: var(--ink-light);
    display: flex;
    align-items: center;
    padding: 0 32px 0 30px;
  }
  .back-brand {
    width: 190px;
    display: flex;
    flex-direction: column;
    align-items: center;
    gap: 10px;
  }
  .card-back .brand-square { background: var(--ink-light); width: 40px; height: 40px; }
  .card-back .brand-name {
    font-weight: 700;
    font-size: 18px;
    letter-spacing: 1px;
    text-transform: uppercase;
    color: var(--ink-light);
    text-align: center;
  }
  .divider {
    width: 1px;
    height: 210px;
    background: var(--ink-light);
    margin: 0 22px 0 14px;
  }
  .contact {
    display: flex;
    flex-direction: column;
    gap: 6px;
    font-size: 12.5px;
    line-height: 1.3;
  }
  .person-name { font-size: 24px; font-weight: 500; line-height: 1.1; }
  .person-role { font-size: 12px; font-weight: 700; margin-bottom: 6px; }
  .contact-row { display: flex; align-items: flex-start; gap: 9px; }
  .contact-row svg { width: 13px; height: 13px; flex: none; margin-top: 2px; }
</style>
</head>
<body>
<main class="canvas">
  <section class="card card-front" aria-label="Card front">
    <div class="brand-lockup">
      <span class="brand-square"></span>
      <span class="brand-name">Veldmark Supplies</span>
    </div>
  </section>

  <section class="card card-back" aria-label="Card back">
    <div class="back-brand">
      <span class="brand-square"></span>
      <span class="brand-name">Veldmark Supplies</span>
    </div>
    <div class="divider"></div>
    <div class="contact">
      <div>
        <div class="person-name">Daniel Hartwell</div>
        <div class="person-role">Owner</div>
      </div>
      <div class="contact-address">412 N Larkspur Ave Suite 3,<br>Midland, TX 79701, United States</div>
      <div class="contact-row">
        <svg viewBox="0 0 16 16" fill="#fff"><path d="M3 1h3l1 4-2 1a9 9 0 0 0 5 5l1-2 4 1v3a2 2 0 0 1-2 2A13 13 0 0 1 1 3a2 2 0 0 1 2-2z"/></svg>
        <span>(555)310-0482</span>
      </div>
      <div class="contact-row">
        <svg viewBox="0 0 16 16" fill="none" stroke="#fff" stroke-width="1.6"><rect x="1" y="3" width="14" height="10"/><path d="M1 3l7 6 7-6"/></svg>
        <span>sales@veldmarksupplies.com</span>
      </div>
      <div class="contact-row">
        <svg viewBox="0 0 16 16" fill="none" stroke="#fff" stroke-width="1.4"><circle cx="8" cy="8" r="6.5"/><path d="M1.5 8h13M8 1.5c-3 3-3 10 0 13M8 1.5c3 3 3 10 0 13"/></svg>
        <span>www.veldmarksupplies.com</span>
      </div>
      <div class="contact-row">
        <svg viewBox="0 0 16 16" fill="none" stroke="#fff" stroke-width="1.6"><circle cx="8" cy="8" r="6.5"/><path d="M8 4v4l3 2"/></svg>
        <span>Monday – Friday<br>8:30am – 5pm</span>
      </div>
    </div>
  </section>
</main>
</body>
</html>
```